Yoga class opening. Little schedule for JUNE JULY and AUGUST

Flyer to promote an opening yoga class. The color of the docx haven't to be respected.

We want something joyfull, professional, clean and serious.

About the logo we oppened a contest at the same time so at the moment there is no logo but the logo color will be simple.

The phone number will change so you can poste a random one for the design that i can change by myself.

i recieved many creation in both side BUT i want something in 1 side :)

Target Market(s)

Yoga student. all age

Industry/Entity Type

It Professional

Logo Text

Yoga fern

Font styles to use
Sans Serif

Requirements
Must have
• The text present on the docx
Nice to have
• Some symbols about yoga ( Namasté signs, mandala, ... )
Should not have
• Not too much details it has to be clear.

```html
<!DOCTYPE html>
<html lang="fr">
<head>
<meta charset="utf-8">
<title>Yoga fern – Flyer ouverture</title>
<link rel="stylesheet" href="https://fonts.googleapis.com/css2?family=Comfortaa:wght@700&family=Oswald:wght@400;500;600&family=Open+Sans:wght@400;600;700&display=swap">
<style>
  :root{
    --purple:#8a2a87;
    --purple-mid:#a981c6;
    --magenta:#b3165f;
    --lavender:#dcd0e8;
    --peach:#f3b97a;
    --sunset-a:#6d4a8e;
    --sunset-b:#e39a6a;
    --sunset-c:#f6d3a2;
    --ink:#4a3556;
    --paper:#ffffff;
    --backdrop:#ebe7e2;
  }
  *{box-sizing:border-box;margin:0;padding:0}
  html,body{width:1200px;height:831px;overflow:hidden;background:var(--backdrop)}
  .flyer{position:absolute;left:320px;top:20px;width:560px;height:792px;background:var(--paper);overflow:hidden;box-shadow:0 4px 18px rgba(0,0,0,.18);font-family:"Open Sans",sans-serif;color:var(--ink)}
  .brand{position:absolute;left:22px;top:16px;display:flex;align-items:center;gap:14px}
  .brand-dot{width:62px;height:62px;border-radius:50%;background:var(--peach)}
  .brand-name{font-family:"Comfortaa",sans-serif;font-weight:700;font-size:54px;color:var(--purple);letter-spacing:1px;line-height:1}
  .tagline{position:absolute;left:98px;top:78px;font-family:"Oswald",sans-serif;font-weight:500;font-size:15px;color:var(--magenta);letter-spacing:.3px}
  .opening{position:absolute;right:18px;top:98px;text-align:right;font-family:"Oswald",sans-serif;font-weight:600;color:var(--purple);line-height:1.1}
  .opening .date{font-size:20px}
  .opening .street{font-size:15px}
  .opening .city{font-size:13px}
  .badge-new{position:absolute;left:0;top:98px;width:196px;height:44px;background:var(--magenta);color:#fff;font-family:"Oswald",sans-serif;font-weight:600;font-size:26px;display:flex;align-items:center;padding-left:18px;clip-path:polygon(0 0,100% 0,90% 100%,0 100%)}
  .hero{position:absolute;left:135px;top:162px;right:0;height:132px;background:linear-gradient(180deg,var(--sunset-a) 0%,var(--sunset-b) 60%,var(--sunset-c) 100%)}
  .schedule{position:absolute;left:0;top:294px;width:330px;bottom:8px;background:var(--lavender)}
  .schedule-intro{background:var(--purple-mid);color:#fff;font-size:10px;line-height:1.35;padding:6px 12px}
  .month{padding:0 12px}
  .month-title{font-family:"Oswald",sans-serif;font-weight:600;font-size:18px;color:var(--magenta);margin-top:8px;line-height:1.2}
  .course{font-family:"Oswald",sans-serif;font-weight:500;font-size:9.5px;color:var(--purple);margin:3px 0 2px;letter-spacing:.2px}
  .slots{list-style:none}
  .slots li{font-size:9.5px;line-height:14.5px;color:var(--ink);border-bottom:1px solid rgba(138,42,135,.18)}
  .emblem{position:absolute;left:378px;top:262px;width:146px;height:146px;border-radius:50%;background:radial-gradient(circle,var(--purple) 0 38%,#fff 39% 52%,#c9a7d8 53% 100%)}
  .info{position:absolute;left:340px;top:428px;width:212px;text-align:center;color:var(--purple);font-size:13.5px;line-height:1.35}
  .info .hl{font-family:"Oswald",sans-serif;font-weight:600;color:var(--magenta);font-size:18px}
  .info .phone{font-family:"Oswald",sans-serif;font-weight:600;color:var(--magenta);font-size:22px;letter-spacing:.5px}
  .info .gap{margin-top:8px}
  .info .page{font-weight:700;color:var(--purple);font-size:15px}
  .farewell{position:absolute;right:0;bottom:8px;width:218px;height:88px;background:var(--magenta);color:#fff;font-family:"Oswald",sans-serif;font-weight:600;font-size:25px;line-height:1.05;display:flex;flex-direction:column;justify-content:center;align-items:center;text-align:center;clip-path:polygon(8% 0,100% 0,100% 100%,0 100%)}
  .base-strip{position:absolute;left:0;right:0;bottom:0;height:8px;background:var(--magenta)}
</style>
</head>
<body>
<main class="flyer">
  <header>
    <div class="brand">
      <span class="brand-dot"></span>
      <span class="brand-name">YOGA FERN</span>
    </div>
    <p class="tagline">NOUVEAU !! VOTRE STUDIO DE YOGA A IXELLES</p>
    <div class="opening">
      <p class="date">OUVERTURE LE 6 JUIN 2016 AU</p>
      <p class="street">212 RUE DES TILLEULS</p>
      <p class="city">1050 IXELLES</p>
    </div>
  </header>

  <div class="badge-new">NOUVEAU !!</div>

  <div class="hero" role="img" aria-label="Photo d'une silhouette en méditation devant des montagnes au coucher du soleil"></div>

  <section class="schedule">
    <p class="schedule-intro">En attendant le planning des cours de la rentrée, YOGA FERN vous propose ses stages et ateliers d'été.</p>

    <div class="month">
      <h2 class="month-title">JUIN</h2>
      <h3 class="course">STAGE DÉCOUVERTE DU YOGA 85 €</h3>
      <ul class="slots">
        <li>Lun 6 – Ven 10 juin 10h00 à 12h00</li>
        <li>Lun 13 – Ven 17 juin 10h00 à 12h00</li>
        <li>Lun 20 – Ven 24 juin 18h00 à 20h00</li>
      </ul>
      <h3 class="course">ATELIER GESTION DU STRESS 20 €</h3>
      <ul class="slots">
        <li>Sam 18 et Dim 19 juin 9h30 à 12h30</li>
        <li>Sam 25 et Dim 26 juin 9h30 à 12h30</li>
      </ul>
    </div>

    <div class="month">
      <h2 class="month-title">JUILLET</h2>
      <h3 class="course">STAGE INITIATION À L'ASHTANGA 85 €</h3>
      <ul class="slots">
        <li>Lun 4 – Ven 8 juil 10h00 à 12h00</li>
        <li>Lun 11 – Ven 15 juil 10h00 à 12h00</li>
        <li>Lun 18 – Ven 22 juil 18h00 à 20h00</li>
      </ul>
      <h3 class="course">ATELIER RESPIRATION 20 €</h3>
      <ul class="slots">
        <li>Sam 9 et Dim 10 juil 9h30 à 12h30</li>
        <li>Sam 23 et Dim 24 juil 9h30 à 12h30</li>
      </ul>
    </div>

    <div class="month">
      <h2 class="month-title">AOUT</h2>
      <h3 class="course">STAGE DÉCOUVERTE DU YOGA 85 €</h3>
      <ul class="slots">
        <li>Lun 1 – Ven 5 août 10h00 à 12h00</li>
        <li>Lun 8 – Ven 12 août 10h00 à 12h00</li>
        <li>Lun 22 – Ven 26 août 18h00 à 20h00</li>
      </ul>
    </div>
  </section>

  <div class="emblem" role="img" aria-label="Symbole Om entouré d'un mandala violet"></div>

  <section class="info">
    <p>Démarrage<br>du planning annuel le</p>
    <p class="hl">5 septembre 2016</p>
    <p class="gap">Plus d'info et inscription :</p>
    <p class="phone">600 123 456</p>
    <p class="gap">Ou via notre page :</p>
    <p class="page">yoga fern</p>
  </section>

  <div class="farewell"><span>UN BEL ETE</span><span>A TOUS !</span></div>
  <div class="base-strip"></div>
</main>
</body>
</html>
```